Business Card design for law firm = Brightvale Australia

We are seeking a new design for our business cards.
We are keeping our logo, which is attached.
We need space for
Name
Title
Address is , which is
Level 7
214 Marlowe Street
Sydney NSW 2047
Phone :
Mobile :
Fax :
Email :
DX :
website www.brightvale-example.com.au

Industry/Entity Type

Law Firm / Banking and Finance

Contact Information for Business Card

We are seeking a new design for our business cards. We are keeping our logo. We need space for Name Title Address is Level 7 214 Marlowe Street Sydney NSW 2047 Phone Mobile Fax Email DX website www.brightvale-example.com.au

Colors
0054AA
0677BA
7BADD7
CADEEF
E8F1F8

Requirements
Must have
• see our website for general feel www.brightvale-example.com.au

```html
<!DOCTYPE html>
<html lang="en">
<head>
<meta charset="utf-8">
<title>Brightvale Australia – Business Card</title>
<link rel="stylesheet" href="https://fonts.googleapis.com/css2?family=Arimo:wght@400;700&family=Tinos&display=swap">
<style>
  :root {
    --bg: #2a2a2c;
    --card-white: #ffffff;
    --card-dark: #161618;
    --brand-blue: #0677ba;
    --bright-blue: #12a3dc;
    --ink: #111111;
    --pattern-light: #6e6e72;
    --pattern-dark: #0a0a0b;
  }
  * { margin: 0; padding: 0; box-sizing: border-box; }
  html, body { width: 1200px; height: 1108px; overflow: hidden; }
  body {
    background: var(--bg);
    position: relative;
    font-family: "Arimo", Arial, sans-serif;
  }
  .card {
    position: absolute;
    top: 250px;
    width: 350px;
    height: 590px;
    border-radius: 18px;
    overflow: hidden;
  }
  .card--front {
    left: 190px;
    background: var(--card-white);
    padding: 120px 30px 40px;
    text-align: center;
  }
  .card--back {
    left: 660px;
    background: var(--card-dark);
  }
  .brand {
    display: flex;
    flex-direction: column;
    align-items: center;
  }
  .brand-name {
    font-family: "Tinos", "Times New Roman", serif;
    font-size: 54px;
    color: var(--brand-blue);
    line-height: 1;
  }
  .brand-tagline {
    margin-top: 12px;
    font-size: 17px;
    letter-spacing: 2px;
    color: var(--bright-blue);
  }
  .person { margin-top: 46px; }
  .person-name {
    font-family: "Tinos", "Times New Roman", serif;
    font-size: 30px;
    color: var(--brand-blue);
    line-height: 1;
  }
  .person-title {
    font-size: 17px;
    color: var(--bright-blue);
    margin-top: 4px;
  }
  .rule {
    width: 90px;
    height: 1px;
    background: var(--ink);
    margin: 12px auto;
  }
  .contact-list {
    list-style: none;
    font-size: 16px;
    line-height: 1.45;
    color: var(--ink);
  }
  .contact-label { font-weight: 700; color: var(--brand-blue); }
  .web-domain { color: var(--brand-blue); }
  .address {
    font-size: 16px;
    line-height: 1.4;
    color: var(--ink);
    font-style: normal;
  }
  .back-pattern {
    position: absolute;
    inset: 0;
    background: linear-gradient(225deg, var(--pattern-light) 0%, #3a3a3d 35%, var(--card-dark) 65%, var(--pattern-dark) 100%);
  }
  .back-brand-name {
    position: absolute;
    right: 56px;
    bottom: 154px;
    font-family: "Tinos", "Times New Roman", serif;
    font-size: 22px;
    color: var(--bright-blue);
  }
</style>
</head>
<body>
  <section class="card card--front" aria-label="Business card front">
    <header class="brand">
      <div class="brand-name">Brightvale</div>
      <div class="brand-tagline">strategic legal outsourcing</div>
    </header>

    <div class="person">
      <div class="person-name">Daniel Hartley</div>
      <div class="person-title">Managing Director</div>
    </div>

    <div class="rule"></div>

    <ul class="contact-list">
      <li><span class="contact-label">P:</span> 044-555 010 234</li>
      <li><span class="contact-label">M:</span> 044-555 010 234</li>
      <li><span class="contact-label">F:</span> 044-555 010 234</li>
      <li><span class="contact-label">E:</span> info@brightvale-example.com</li>
      <li><span class="contact-label">DX</span> :000987654321</li>
      <li>www.<span class="web-domain">brightvale-example</span>.com.au</li>
    </ul>

    <div class="rule"></div>

    <address class="address">
      Level 7, 214 Marlowe Street<br>
      Sydney NSW 2047
    </address>
  </section>

  <section class="card card--back" aria-label="Business card back">
    <div class="back-pattern" role="img" aria-label="Glossy grid of dark grey squares fading from light grey at top right to black at bottom left"></div>
    <div class="back-brand-name">Brightvale</div>
  </section>
</body>
</html>
```